Android App Design Project

Hi my name is Nadir, and I'm an android developer. I'm searching for a professional designer that can design my app.I have already launched the app and you can find it in the apptrove bazaar.

Main Requirements
- 15 sport icons
- 6 android pages
- Action bar
- Buttons and other icons

You need to do all requirements to submit a design. I need the design in both JPEG format and Photoshop PSD format. If you are interested then please download the PDF file ,it will help you a lot.
The name of the app is "MATCH VIEW Classic" you can find it in Orbix Shelf.

NOTICE: You might read that the Payment is not guaranteed if I'm not happy with the design BUT if you make a good design and you win the contest, then you become my main designer that means if I want to change or add something to the design of the app in the future I return to you "the winner" directly to make the redesign and get paid for it.

Regards.
Skype: Fadi Hamoudi "fadi48"
E-mail: fadinadir@quillpost.net

Industry/Entity Type

Tv

Requirements
Must have
• - 15 sport icons
- 6 android pages
- Action bar
- Buttons and other icons

```html
<!DOCTYPE html>
<html lang="en">
<head>
<meta charset="utf-8">
<title>Sports</title>
<link href="https://fonts.googleapis.com/css2?family=PT+Sans+Narrow:wght@400;700&display=swap" rel="stylesheet">
<style>
  :root {
    --bar-top: #f9a03a;
    --bar-bottom: #e8641c;
    --bar-edge: #b84a10;
    --btn-top: #f07a2a;
    --btn-bottom: #d4531a;
    --seg-active: #c2460f;
    --bg: #262626;
    --bg-dot: #2f2f2f;
    --label: #ffffff;
    --glyph: rgba(20, 20, 20, 0.55);
  }
  * { box-sizing: border-box; margin: 0; padding: 0; }
  html, body { width: 817px; height: 1200px; overflow: hidden; }
  body {
    position: relative;
    background-color: var(--bg);
    background-image: radial-gradient(var(--bg-dot) 1.5px, transparent 1.6px);
    background-size: 7px 7px;
    font-family: "PT Sans Narrow", "Arial Narrow", sans-serif;
  }
  .action-bar {
    position: absolute; left: 0; top: 0; width: 817px; height: 102px;
    background: linear-gradient(var(--bar-top), var(--bar-bottom));
    border-bottom: 3px solid var(--bar-edge);
  }
  .bar-button {
    position: absolute; top: 23px; height: 56px; width: 84px;
    border-radius: 12px;
    background: linear-gradient(var(--btn-top), var(--btn-bottom));
    border: 2px solid rgba(255,255,255,0.45);
    box-shadow: inset 0 2px 3px rgba(0,0,0,0.25);
    display: flex; align-items: center; justify-content: center;
    color: #fff;
  }
  .back-button { left: 10px; }
  .info-button { left: 705px; font-family: Georgia, serif; font-style: italic; font-weight: 700; font-size: 40px; }
  .segmented {
    position: absolute; left: 220px; top: 23px; width: 377px; height: 56px;
    border-radius: 12px; overflow: hidden; display: flex;
    border: 2px solid rgba(255,255,255,0.45);
    background: linear-gradient(var(--btn-top), var(--btn-bottom));
  }
  .segment {
    flex: 1; display: flex; align-items: center; justify-content: center;
    color: #fff; font-size: 30px; font-weight: 700;
  }
  .segment + .segment { border-left: 2px solid rgba(255,255,255,0.35); }
  .segment.is-active { background: var(--seg-active); box-shadow: inset 0 3px 6px rgba(0,0,0,0.35); }
  .sport {
    position: absolute; width: 190px; height: 190px; margin: -95px 0 0 -95px;
    border-radius: 50%;
    background:
      radial-gradient(ellipse 60% 40% at 50% 18%, rgba(255,255,255,0.55), transparent 70%),
      radial-gradient(circle at 50% 45%, var(--c) 50%, var(--d) 100%);
    box-shadow: 0 6px 10px rgba(0,0,0,0.6), inset 0 -8px 14px rgba(0,0,0,0.25);
  }
  .sport-glyph {
    position: absolute; left: 65px; top: 32px; width: 60px; height: 80px;
    border-radius: 10px; background: var(--glyph);
  }
  .sport-label {
    position: absolute; left: 0; right: 0; top: 126px; text-align: center;
    color: var(--label); font-size: 28px; line-height: 29px;
    text-shadow: 0 2px 3px rgba(0,0,0,0.6);
  }
  .sport-label.two-line { top: 118px; }
</style>
</head>
<body>
  <header class="action-bar">
    <div class="bar-button back-button" aria-label="Back">
      <svg width="44" height="30" viewBox="0 0 44 30"><path d="M2 15 L18 2 V10 H42 V20 H18 V28 Z" fill="#fff"/></svg>
    </div>
    <nav class="segmented">
      <div class="segment">Latest</div>
      <div class="segment is-active">Score</div>
    </nav>
    <div class="bar-button info-button" aria-label="Info">i</div>
  </header>

  <main class="sport-grid">
    <div class="sport" style="left:112px;top:212px;--c:#5cc21c;--d:#2e7a08"><div class="sport-glyph" role="img" aria-label="Badminton player silhouette"></div><div class="sport-label">Badminton</div></div>
    <div class="sport" style="left:408px;top:212px;--c:#2296f2;--d:#0a4fa8"><div class="sport-glyph" role="img" aria-label="Ice hockey player silhouette"></div><div class="sport-label">Ice Hocky</div></div>
    <div class="sport" style="left:705px;top:212px;--c:#d48c12;--d:#7a4c04"><div class="sport-glyph" role="img" aria-label="Cricket player silhouette"></div><div class="sport-label">Cricket</div></div>

    <div class="sport" style="left:112px;top:429px;--c:#e8521e;--d:#8a2006"><div class="sport-glyph" role="img" aria-label="Football player silhouette"></div><div class="sport-label">Football</div></div>
    <div class="sport" style="left:408px;top:429px;--c:#a89044;--d:#5a4a18"><div class="sport-glyph" role="img" aria-label="Volleyball player silhouette"></div><div class="sport-label">Volleyball</div></div>
    <div class="sport" style="left:705px;top:429px;--c:#2db67c;--d:#0e6a40"><div class="sport-glyph" role="img" aria-label="Boxer silhouette"></div><div class="sport-label">Boxing</div></div>

    <div class="sport" style="left:112px;top:646px;--c:#3c92ec;--d:#0e4ca4"><div class="sport-glyph" role="img" aria-label="Basketball player silhouette"></div><div class="sport-label">Basketball</div></div>
    <div class="sport" style="left:408px;top:646px;--c:#a4a4a4;--d:#4e4e4e"><div class="sport-glyph" role="img" aria-label="Tennis player silhouette"></div><div class="sport-label">Tennis</div></div>
    <div class="sport" style="left:705px;top:646px;--c:#d8449e;--d:#7a1258"><div class="sport-glyph" role="img" aria-label="Handball player silhouette"></div><div class="sport-label">Handball</div></div>

    <div class="sport" style="left:112px;top:863px;--c:#e44c5e;--d:#8a1424"><div class="sport-glyph" role="img" aria-label="Snowflake symbol"></div><div class="sport-label">Wintersport</div></div>
    <div class="sport" style="left:408px;top:863px;--c:#30a864;--d:#0c5a2c"><div class="sport-glyph" role="img" aria-label="Rugby player silhouette"></div><div class="sport-label">Rugby</div></div>
    <div class="sport" style="left:705px;top:863px;--c:#ec5420;--d:#8c2206"><div class="sport-glyph" role="img" aria-label="Futsal player silhouette"></div><div class="sport-label">Futsal</div></div>

    <div class="sport" style="left:112px;top:1080px;--c:#c4747c;--d:#6a3038"><div class="sport-glyph" role="img" aria-label="Dartboard target"></div><div class="sport-label">Darts</div></div>
    <div class="sport" style="left:408px;top:1080px;--c:#ecac1c;--d:#8c5c04"><div class="sport-glyph" role="img" aria-label="Wrestlers silhouette"></div><div class="sport-label">Wrestling</div></div>
    <div class="sport" style="left:705px;top:1080px;--c:#3cae3c;--d:#12601a"><div class="sport-glyph" role="img" aria-label="American football player silhouette"></div><div class="sport-label two-line">American<br>Football</div></div>
  </main>
</body>
</html>
```